Coastline Premier Retreats Business Card Design

Design a business card for Coastline Premier Retreats. Look at the website for colors and reference. Card should have logo, name, title, office number, mobile number, email, URL and a tagline like, "Luxury Hotel & Resort Email Marketing" (This might change).

https://www.coastlinepremierretreats.example

The rest I will leave up to your imagination.

Contact Information for Business Card

Logo, name, title, office number, mobile number, email, URL and a tagline like, "Luxury Hotel & Resort Email Marketing" (This might change).

```html
<!DOCTYPE html>
<html lang="en">
<head>
<meta charset="utf-8">
<title>Coastline Premier Retreats – Business Card</title>
<link href="https://fonts.googleapis.com/css2?family=Arimo:wght@400;700&family=Montserrat:wght@400&display=swap" rel="stylesheet">
<style>
  :root {
    --bg: #1b1b1b;
    --card-front: #1f1f1f;
    --card-back: #161616;
    --accent: #ee6c14;
    --text: #f2f2f2;
    --emboss: #3b3b3b;
  }
  * { margin: 0; padding: 0; box-sizing: border-box; }
  html, body {
    width: 1200px; height: 1059px; overflow: hidden;
    background: var(--bg);
    font-family: "Arimo", Arial, sans-serif;
    color: var(--text);
  }
  .card {
    position: absolute;
    width: 688px; height: 390px;
  }
  .card--front { left: 257px; top: 89px; background: var(--card-front); }
  .card--back { left: 255px; top: 546px; background: var(--card-back); }

  .frame {
    position: absolute; left: 23px; top: 22px; width: 640px; height: 335px;
    border: 2px solid var(--accent); border-bottom: none;
  }
  .frame-bottom {
    position: absolute; top: 355px; height: 2px; background: var(--accent);
  }
  .frame-bottom--left { left: 23px; width: 155px; }
  .frame-bottom--right { left: 509px; width: 154px; }
  .tagline {
    position: absolute; left: 178px; width: 331px; top: 345px;
    text-align: center; font-size: 17.5px; line-height: 20px; color: var(--text);
  }

  .brand {
    position: absolute; left: 59px; top: 182px; width: 262px;
    display: flex; align-items: center; gap: 9px;
  }
  .brand-mark { width: 12px; height: 12px; background: var(--accent); flex: none; }
  .brand-name {
    font-weight: 700; font-size: 14px; letter-spacing: 0.5px;
    text-transform: uppercase; color: var(--text); white-space: nowrap;
  }

  .divider {
    position: absolute; left: 340px; top: 101px; width: 1px; height: 189px;
    background: var(--accent);
  }
  .details { position: absolute; left: 366px; top: 96px; width: 288px; }
  .person-name {
    font-weight: 700; font-size: 28.5px; line-height: 30px;
    color: var(--accent); letter-spacing: 0.4px;
  }
  .person-title {
    font-family: "Montserrat", Arial, sans-serif;
    font-size: 16px; line-height: 20px; letter-spacing: 0.3px;
  }
  .address { font-size: 16px; line-height: 20.5px; margin-top: 13px; }
  .contacts { list-style: none; margin-top: 11px; }
  .contacts li {
    display: flex; align-items: center; font-size: 15px; line-height: 21.3px;
    white-space: nowrap;
  }
  .contacts svg { width: 12px; height: 12px; margin-right: 6px; fill: var(--accent); flex: none; }

  .back-brand {
    position: absolute; left: 0; right: 0; top: 174px;
    display: flex; justify-content: center; align-items: center; gap: 14px;
  }
  .back-brand .brand-mark { width: 22px; height: 22px; background: var(--emboss); }
  .back-brand .brand-name { font-size: 27px; letter-spacing: 1.2px; color: var(--emboss); }
</style>
</head>
<body>
  <section class="card card--front">
    <div class="frame"></div>
    <div class="frame-bottom frame-bottom--left"></div>
    <div class="frame-bottom frame-bottom--right"></div>
    <p class="tagline">Luxury Hotel &amp; Resort Email Marketing</p>

    <div class="brand">
      <span class="brand-mark"></span>
      <span class="brand-name">Coastline Premier Retreats</span>
    </div>

    <div class="divider"></div>

    <div class="details">
      <h1 class="person-name">DANIEL MARSH</h1>
      <p class="person-title">CEO/Founder</p>
      <p class="address">Po Box, 482 B Harbor Rd<br>North America, AB 51920</p>
      <ul class="contacts">
        <li>
          <svg viewBox="0 0 12 12" aria-hidden="true"><path d="M3 0h6a1 1 0 0 1 1 1v10a1 1 0 0 1-1 1H3a1 1 0 0 1-1-1V1a1 1 0 0 1 1-1zm0 1.5v7.5h6V1.5zm3 8.3a.8.8 0 1 0 0 1.6.8.8 0 0 0 0-1.6z"/></svg>
          555.214.7300
        </li>
        <li>
          <svg viewBox="0 0 12 12" aria-hidden="true"><path d="M0 4.5C0 2.5 3 1.5 6 1.5s6 1 6 3v1H9V4H3v1.5H0zM2.5 6h7l1 4.5h-9zm3.5 1a1.3 1.3 0 1 0 0 2.6A1.3 1.3 0 0 0 6 7z"/></svg>
          +34 600 555 274
        </li>
        <li>
          <svg viewBox="0 0 12 12" aria-hidden="true"><path d="M0 5l6-4 6 4v6.5H0zm1.5 1v4l3-2zm9 0l-3 2 3 2zM6 8.8L2.3 10.5h7.4z"/></svg>
          info@coastlinepremierretreats.example
        </li>
        <li>
          <svg viewBox="0 0 12 12" aria-hidden="true"><path d="M6 0a6 6 0 1 0 0 12A6 6 0 0 0 6 0zm-.5 1.5L4 3l1 1.5-2 1L1.6 5A4.5 4.5 0 0 1 5.5 1.5zM7 10.4V9l1.5-1.5L8 6l2.4-.5A4.5 4.5 0 0 1 7 10.4z"/></svg>
          www.coastlinepremierretreats.example
        </li>
      </ul>
    </div>
  </section>

  <section class="card card--back">
    <div class="back-brand">
      <span class="brand-mark"></span>
      <span class="brand-name">Coastline Premier Retreats</span>
    </div>
  </section>
</body>
</html>
```